Harborview Estates Business Card for Apartment Buildings

Create business cards for resident managers who run apartment buildings. The audience is the public who are searching for apartment rentals, and current residents who live at the apartment building. Key design element will be incorporating the company logo, however, the logo cannot dominate. The building name and manager name are more important than the logo. Current business card design leaves little room for copy, so we may need to reduce the size on the current card to allow for more space for copy.

Target Market(s)

Adults 18-65 years of age, who are looking for an apartment rental, plus current residents who live at our apartment buildings.

Industry/Entity Type

Property Management

Contact Information for Business Card

A major design element will be use of the company logo. Important property and manager contact information must be part of the design. The size of the logo will need to be reduced to make room for building and manager contact copy.

Font styles to use
Sans Serif

Colors
3176b5
000000
959595
ffffff

Requirements
Must have
• 1) Incorporate the company logo.
• 2) Use the company colors (dark blue, black/grey, over white).
• 3) FEATURE THE BUILDING NAME
• 4) FEATURE THE MANAGER NAME
• 5) The company name is less important than BUILDING and MANAGER
• 6) Manager contact information
• **SEE ATTACHED CREATIVE BRIEF**
Nice to have
• 1) Back of card logo watermark
• 2) Ability to write notes on back of carfd
Should not have
• Avoid letting the company logo dominate the card, the building name and manager are more important than the company logo.

```html
<!DOCTYPE html>
<html lang="en">
<head>
<meta charset="utf-8">
<title>Harborview Estates Business Card</title>
<link href="https://fonts.googleapis.com/css2?family=Open+Sans:wght@400;600;700&display=swap" rel="stylesheet">
<style>
  :root{
    --brand-blue:#3176b5;
    --ink:#000000;
    --grey:#959595;
    --white:#ffffff;
    --card-dark:#3a3b3e;
    --backdrop:#e4e4e4;
    --text-dark:#333333;
  }
  *{box-sizing:border-box;margin:0;padding:0}
  html,body{width:1200px;height:862px;overflow:hidden}
  body{background:var(--backdrop);font-family:"Open Sans",Arial,sans-serif;position:relative}
  .card{position:absolute;width:620px;height:354px;border-radius:22px;overflow:hidden;box-shadow:0 10px 26px rgba(0,0,0,.22)}
  .card-back{left:60px;top:70px;background:var(--card-dark)}
  .card-front{left:520px;top:440px;background:var(--white)}

  .brand{display:flex;align-items:center;gap:14px}
  .brand-dot{width:34px;height:34px;border-radius:50%;background:var(--brand-blue);flex:none}
  .brand-name{font-weight:700;color:var(--brand-blue);line-height:1.05;letter-spacing:.5px}
  .card-back .brand{position:absolute;left:0;right:0;top:128px;justify-content:center}
  .card-back .brand-name{font-size:34px}
  .brand-name small{display:block;font-size:.55em;letter-spacing:4px}
  .website{position:absolute;left:0;right:0;top:262px;text-align:center;color:var(--brand-blue);font-size:15px;letter-spacing:.5px}

  .card-front .brand{position:absolute;left:40px;top:130px}
  .card-front .brand-name{font-size:26px}
  .divider{position:absolute;left:340px;top:40px;width:1px;height:180px;background:var(--grey)}
  .manager{position:absolute;left:366px;top:44px}
  .manager-name{font-size:21px;font-weight:700;color:var(--brand-blue)}
  .manager-title{font-size:13px;color:var(--grey);margin-bottom:14px}
  .contact-list{list-style:none}
  .contact-list li{display:flex;align-items:center;gap:9px;font-size:13px;color:var(--text-dark);line-height:25px}
  .contact-list svg{width:13px;height:13px;fill:var(--brand-blue);flex:none}
  .address-band{position:absolute;left:0;right:0;bottom:32px;height:40px;background:var(--brand-blue);color:var(--white);font-size:14px;display:flex;align-items:center;padding-left:40px;letter-spacing:.3px}
</style>
</head>
<body>
  <section class="card card-back">
    <div class="brand">
      <span class="brand-dot"></span>
      <div class="brand-name">HARBORVIEW<small>ESTATES LLC</small></div>
    </div>
    <p class="website">www.harborviewestates.us</p>
  </section>

  <section class="card card-front">
    <div class="brand">
      <span class="brand-dot"></span>
      <div class="brand-name">HARBORVIEW<small>ESTATES LLC</small></div>
    </div>
    <div class="divider"></div>
    <div class="manager">
      <h1 class="manager-name">Marisol Delgado</h1>
      <p class="manager-title">Resident Manager</p>
      <ul class="contact-list">
        <li><svg viewBox="0 0 24 24"><path d="M6.6 10.8a15.1 15.1 0 0 0 6.6 6.6l2.2-2.2c.3-.3.7-.4 1-.2 1.1.4 2.3.6 3.6.6.6 0 1 .4 1 1V20c0 .6-.4 1-1 1A17 17 0 0 1 3 4c0-.6.4-1 1-1h3.5c.6 0 1 .4 1 1 0 1.3.2 2.5.6 3.6.1.3 0 .7-.2 1z"/></svg>555-214-0187</li>
        <li><svg viewBox="0 0 24 24"><path d="M6 3h10v5H6zM3 9h18v9h-3v3H6v-3H3zm5 7v3h8v-3z"/></svg>555-308-4421</li>
        <li><svg viewBox="0 0 24 24"><path d="M7 1h10a2 2 0 0 1 2 2v18a2 2 0 0 1-2 2H7a2 2 0 0 1-2-2V3a2 2 0 0 1 2-2zm0 3v14h10V4zm5 15.5a1 1 0 1 0 0 2 1 1 0 0 0 0-2z"/></svg>555-690-3350</li>
        <li><svg viewBox="0 0 24 24"><path d="M2 5h20v14H2zm2 2v.5l8 5 8-5V7zm0 2.8V17h16V9.8l-8 5z"/></svg>marisol@harborviewest.com</li>
      </ul>
    </div>
    <div class="address-band">Cedar Court Apartments - 1425 Linden Avenue Riverside, CA 92501</div>
  </section>
</body>
</html>
```